Stylish Business Cards Wanted

- DOUBLE SIDED Design Required -

High end, edgy cards for a corporate and personal stylist. Must include logo,
Name: Belinda Harwick
Title: Director and Stylist
telephone : +61 8 7142 5809
email: belinda@theloombriefing.example
website: theloombriefing.example
Tag: Corporate Workwear & Uniform Specialist | Personal Stylist
Would like nice icons for telephone, email, website

Target Market(s)

Businesses wanting stylish uniforms, people wanting stylish wardrobes

Industry/Entity Type

Corporate Workwear Stylist

Contact Information for Business Card

I would like black, white and gold foiling incorporated in the design - possibly a touch of the other colours on my branding guide attached Name: Belinda Harwick Title: Director and Stylist telephone : +61 8 7142 5809 email: belinda@theloombriefing.example website: theloombriefing.example Tag: Corporate Workwear & Uniform Specialist | Personal Stylist Would like nice icons for telephone, email, website

Font styles to use
Other font styles liked:
• Raleway

Colors

Designer to choose colors to be used in the design.

Requirements
Must have
• Gold foil accents

```html
<!DOCTYPE html>
<html lang="en">
<head>
<meta charset="utf-8">
<title>The Loom Briefing – Business Card</title>
<link href="https://fonts.googleapis.com/css2?family=Raleway:wght@500;600;700&family=Arimo:wght@400&display=swap" rel="stylesheet">
<style>
  :root {
    --bg: #ece9e4;
    --card: #ffffff;
    --ink: #3a3a3c;
    --charcoal: #353537;
    --gold: #e3bb5c;
    --white: #ffffff;
  }
  * { box-sizing: border-box; margin: 0; padding: 0; }
  html, body { width: 1200px; height: 900px; overflow: hidden; background: var(--bg); }
  .canvas { position: relative; width: 1200px; height: 900px; }
  .card {
    position: absolute; left: 250px; width: 700px; height: 400px;
    background: var(--card); overflow: hidden;
    box-shadow: 0 6px 18px rgba(0,0,0,0.12);
  }
  .card--front { top: 30px; }
  .card--back { top: 470px; }
  .wordmark {
    font-family: "Raleway", sans-serif; font-weight: 700; color: var(--ink);
    letter-spacing: 0.04em; white-space: nowrap;
  }
  .card--front .wordmark {
    position: absolute; left: 0; right: 0; top: 178px; text-align: center; font-size: 40px;
  }
  .card--back .wordmark {
    position: absolute; right: 48px; top: 72px; font-size: 30px;
  }
  .waves { position: absolute; inset: 0; width: 700px; height: 400px; }
  .person { position: absolute; left: 70px; top: 118px; }
  .person__name {
    font-family: "Raleway", sans-serif; font-weight: 600; color: var(--gold);
    font-size: 17px; letter-spacing: 0.2em; text-transform: uppercase;
  }
  .person__title {
    font-family: "Raleway", sans-serif; font-weight: 500; color: var(--ink);
    font-size: 10px; margin-top: 2px; letter-spacing: 0.02em;
  }
  .contacts { position: absolute; left: 72px; top: 186px; list-style: none; }
  .contacts li {
    display: flex; align-items: center; gap: 12px; height: 28px;
    font-family: "Arimo", sans-serif; font-size: 15px; color: var(--ink);
  }
  .contacts svg { width: 16px; height: 16px; flex: none; }
  .address {
    position: absolute; right: 44px; top: 248px; text-align: right;
    font-family: "Arimo", sans-serif; font-size: 18px; line-height: 1.3; color: var(--white);
  }
</style>
</head>
<body>
<div class="canvas">

  <section class="card card--front" aria-label="Card front">
    <div class="wordmark">The Loom Briefing</div>
  </section>

  <section class="card card--back" aria-label="Card back">
    <svg class="waves" viewBox="0 0 700 400" aria-hidden="true">
      <path fill="var(--gold)" d="M0,300 C150,345 330,325 490,238 C360,322 170,348 0,326 Z"/>
      <path fill="var(--charcoal)" d="M0,340 C180,372 380,342 520,262 C600,218 650,200 700,188 L700,400 L0,400 Z"/>
    </svg>

    <div class="wordmark">The Loom Briefing</div>

    <div class="person">
      <div class="person__name">Belinda Harwick</div>
      <div class="person__title">Director and Stylist</div>
    </div>

    <ul class="contacts">
      <li>
        <svg viewBox="0 0 24 24"><path fill="var(--gold)" d="M6.6 10.8a15 15 0 0 0 6.6 6.6l2.2-2.2c.3-.3.7-.4 1-.2 1.1.4 2.3.6 3.6.6.6 0 1 .4 1 1V20c0 .6-.4 1-1 1A17 17 0 0 1 3 4c0-.6.4-1 1-1h3.5c.6 0 1 .4 1 1 0 1.3.2 2.5.6 3.6.1.3 0 .7-.2 1z"/></svg>
        +61 8 7142 5809
      </li>
      <li>
        <svg viewBox="0 0 24 24"><rect x="6" y="2" width="12" height="20" rx="2" fill="none" stroke="var(--gold)" stroke-width="2"/><circle cx="12" cy="18" r="1.2" fill="var(--gold)"/></svg>
        +61 4 1187 2236
      </li>
      <li>
        <svg viewBox="0 0 24 24"><rect x="2" y="5" width="20" height="14" fill="var(--gold)"/><path d="M2 5l10 8 10-8" fill="none" stroke="var(--white)" stroke-width="1.5"/></svg>
        belinda@theloombriefing.example
      </li>
      <li>
        <svg viewBox="0 0 24 24" fill="none" stroke="var(--gold)" stroke-width="1.6"><circle cx="12" cy="12" r="9.5"/><ellipse cx="12" cy="12" rx="4.5" ry="9.5"/><path d="M2.5 12h19M4 7h16M4 17h16"/></svg>
        theloombriefing.example
      </li>
    </ul>

    <div class="address">48 Carrow Lane<br>Norwood, SA, AU</div>
  </section>

</div>
</body>
</html>
```